Upscale business cards needed for Board of Directors

We need professional business cards created for members of our family business Board of Directors. We would like these relatively simple and straightforward, but also with a unique element to set them apart. Probably stick with neutral and simple colors - white, grey etc. We need space for the traditional elements, including name, title, address, email/phone number. And we will be creating several from this template so it needs to be template that is easy to switch information in and out of.
Business
See description

```html
<!DOCTYPE html>
<html lang="en">
<head>
<meta charset="utf-8">
<title>Harborline Holdings – Business Cards</title>
<link href="https://fonts.googleapis.com/css2?family=Lato:wght@400;900&display=swap" rel="stylesheet">
<style>
  :root {
    --ink: #0b0b0b;
    --paper: #ffffff;
    --gold: #b5a47a;
    --stage: #3a3a3a;
    --muted: #222222;
  }
  * { box-sizing: border-box; margin: 0; padding: 0; }
  html, body {
    width: 1200px;
    height: 900px;
    overflow: hidden;
    background: var(--stage);
    font-family: "Lato", sans-serif;
  }
  .stage {
    width: 1200px;
    height: 900px;
    display: flex;
    flex-direction: column;
    align-items: center;
    justify-content: center;
    gap: 50px;
  }
  .card {
    position: relative;
    width: 640px;
    height: 366px;
    overflow: hidden;
    box-shadow: 0 10px 28px rgba(0,0,0,0.45);
  }
  .card--back { background: var(--ink); color: var(--paper); }
  .card--front { background: var(--paper); color: var(--ink); }

  .brand-name {
    font-weight: 900;
    text-transform: uppercase;
    line-height: 1;
  }
  .brand-name__main { display: block; font-size: 56px; letter-spacing: 1px; }
  .brand-name__sub { display: block; font-size: 26px; letter-spacing: 14px; margin-top: 6px; }

  .card--back .brand-name {
    position: absolute;
    left: 0; right: 0; top: 108px;
    text-align: center;
  }
  .card--back .website {
    position: absolute;
    left: 0; right: 0; top: 282px;
    text-align: center;
    font-size: 16px;
    letter-spacing: 1.5px;
  }

  .card--front .brand-name {
    position: absolute;
    left: 34px; top: 92px;
  }
  .card--front .brand-name__main { font-size: 50px; }
  .card--front .brand-name__sub { font-size: 23px; letter-spacing: 12px; }

  .card__bands { position: absolute; left: 0; top: 0; }
  .card--front .website {
    position: absolute;
    left: 34px; top: 296px;
    font-size: 16px;
    letter-spacing: 1.5px;
    color: var(--paper);
  }

  .contact {
    position: absolute;
    left: 400px; top: 96px;
    font-size: 17px;
    line-height: 1.2;
  }
  .contact__name { font-size: 21px; }
  .contact__title { color: var(--gold); font-size: 17px; margin-bottom: 12px; }
  .contact__address { margin-bottom: 12px; }
  .contact__row { display: flex; align-items: center; gap: 10px; }
  .contact__icon { width: 14px; height: 14px; flex: none; }
</style>
</head>
<body>
<main class="stage">

  <section class="card card--back" aria-label="Card back">
    <div class="brand-name">
      <span class="brand-name__main">Harborline</span>
      <span class="brand-name__sub">Holdings</span>
    </div>
    <p class="website">www.harborline.com</p>
  </section>

  <section class="card card--front" aria-label="Card front">
    <svg class="card__bands" width="640" height="366" viewBox="0 0 640 366" aria-hidden="true">
      <polygon points="0,282 640,282 640,366 0,366" fill="var(--ink)"/>
      <polygon points="0,334 330,334 350,314 640,314 640,366 0,366" fill="var(--gold)"/>
      <polygon points="350,282 640,282 640,306 346,306" fill="var(--paper)"/>
    </svg>

    <div class="brand-name">
      <span class="brand-name__main">Harborline</span>
      <span class="brand-name__sub">Holdings</span>
    </div>

    <p class="website">www.harborline.com</p>

    <div class="contact">
      <p class="contact__name">Daniel Whitford</p>
      <p class="contact__title">Director</p>
      <p class="contact__address">1450 Oak Ridge Dr<br>Marlow TX 78000</p>
      <p class="contact__row">
        <svg class="contact__icon" viewBox="0 0 16 16" aria-hidden="true"><path d="M3 1l3 3-1.5 2a9 9 0 0 0 5.5 5.5L12 10l3 3-2 2C7 15 1 9 1 3z" fill="var(--gold)"/></svg>
        512 555 0140
      </p>
      <p class="contact__row">
        <svg class="contact__icon" viewBox="0 0 16 16" aria-hidden="true"><rect x="4" y="1" width="8" height="4" fill="var(--gold)"/><rect x="1" y="6" width="14" height="6" rx="1" fill="var(--gold)"/><rect x="4" y="10" width="8" height="5" fill="var(--gold)"/></svg>
        512 555 0141
      </p>
      <p class="contact__row">
        <svg class="contact__icon" viewBox="0 0 16 16" aria-hidden="true"><rect x="1" y="3" width="14" height="10" fill="var(--gold)"/><polyline points="1,3 8,9 15,3" fill="none" stroke="var(--paper)" stroke-width="1.3"/></svg>
        info@harborline.com
      </p>
    </div>
  </section>

</main>
</body>
</html>
```